Website for "Bright Morrow Ltd" cleaning bsuiness

We require a website to expose our business to the local market. We want to provide background on who we are and what we do but in an easily digestible way. We clean domestic and commercial premises and want to provide a list of all of our services to potential customers. We operate out of Warrington in the UK.

We would like the website to be animated in some way so that the experience of using it is not dull or mundane. This website needs to be an extension of our company.

Target Market(s)

30 - 60 year olds for Domestic plus commercial clients

Industry/Entity Type

Cleaning Service

Coding

Coded - Design and coding required

Number of Pages Required

4 page

Font styles to use
Sans Serif

Colors
0455a3
3176b5
85acd3
cfdeed
ffffff
000000
1b1b1b
c8c8c8
757575

Requirements
Must have
• Logo which has been provided. Theme based around the logo and its colours. Simple layout to avoid confusion.
Nice to have
• Animations where possible to impress the customer.
Should not have
• any pictures of cleaning equipment, fairies, maids etc

```html
<!DOCTYPE html>
<html lang="en">
<head>
<meta charset="utf-8">
<title>Bright Morrow Ltd – Professional Cleaning Service</title>
<link href="https://fonts.googleapis.com/css2?family=Noto+Serif&family=Open+Sans:wght@400;600&family=Raleway:wght@400;500&family=Roboto:wght@400;500;700&family=Roboto+Condensed:wght@400;700&display=swap" rel="stylesheet">
<style>
:root{
  --navy:#0a3a9c;
  --royal:#1f4fb0;
  --sky:#3394f5;
  --sky-dark:#0a46a8;
  --ink:#1b1b1b;
  --grey:#757575;
  --line:#c8c8c8;
  --panel:#e4e5e7;
  --white:#ffffff;
}
*{margin:0;padding:0;box-sizing:border-box}
h1,h2,h3,h4{font-weight:400}
html,body{width:1200px;height:2903px;overflow:hidden;background:var(--white)}
body{position:relative;font-family:"Open Sans",sans-serif;color:var(--ink)}
.abs{position:absolute}
.hero{left:0;top:0;width:1200px;height:509px;background:linear-gradient(180deg,#d9dde1 0%,#c9d0d6 55%,#b9c3cc 100%)}
.brand{position:absolute;display:flex;align-items:center;gap:10px;font-family:"Roboto",sans-serif;font-weight:700;white-space:nowrap}
.brand-hero{left:490px;top:170px;font-size:38px;color:var(--navy)}
.brand-dot{border-radius:50%;background:var(--sky)}
.nav{left:0;top:509px;width:1200px;height:64px;background:var(--sky);font-family:"Roboto",sans-serif;font-size:21px;color:var(--white)}
.nav a{position:absolute;top:0;height:64px;line-height:64px;color:var(--white);text-decoration:none;transform:translateX(-50%)}
.nav .active{left:77px;width:128px;transform:none;text-align:center;background:var(--sky-dark)}
.welcome-title{left:0;top:622px;width:1200px;text-align:center;font-family:"Noto Serif",serif;font-size:35px;color:var(--navy)}
.welcome-title span,.section-title span{color:var(--sky)}
.welcome-text{left:276px;top:683px;width:648px;text-align:center;font-size:16px;line-height:25px;color:var(--grey)}
.btn{left:493px;top:795px;width:217px;height:62px;line-height:62px;text-align:center;background:var(--sky);color:var(--white);font-family:"Roboto",sans-serif;font-size:19px;border-radius:3px}
.domestic{left:0;top:911px;width:1200px;height:728px;background:linear-gradient(90deg,#2a55b4,#2d5cbc 50%,#2650ab)}
.domestic-title{left:0;top:948px;width:1200px;text-align:center;font-family:"Noto Serif",serif;font-size:33px;color:var(--white)}
.service-photo{width:166px;height:166px;border-radius:50%;border:3px solid var(--white);box-shadow:0 0 0 2px #13245a}
.dom-label{width:300px;text-align:center;color:var(--white);font-family:"Roboto",sans-serif}
.dom-label h3{font-size:21px;margin-bottom:10px}
.dom-label p{font-size:15px;line-height:24px}
.hub{left:521px;top:1175px;width:158px;height:158px;border-radius:50%;background:var(--white);display:flex;align-items:center;justify-content:center;font-family:"Roboto",sans-serif;font-weight:700;font-size:21px;color:var(--navy);text-align:center;line-height:24px}
.section-title{left:0;top:1688px;width:1200px;text-align:center;font-family:"Noto Serif",serif;font-size:33px;color:var(--navy)}
.card{width:240px;top:1767px}
.card-photo{width:240px;height:166px}
.card h3{margin-top:20px;font-family:"Roboto",sans-serif;font-size:21px;color:var(--navy)}
.card p{margin-top:10px;font-size:15px;line-height:25px;color:var(--ink)}
.more{margin-top:10px;display:flex;align-items:center;gap:10px;font-family:"Raleway",sans-serif;font-size:14px;color:var(--sky)}
.call-grey{left:580px;top:2129px;width:542px;height:145px;background:var(--panel)}
.call-text{left:634px;top:2150px;width:460px;font-size:16px;line-height:25px;color:var(--grey)}
.call-mail{left:634px;top:2211px;display:flex;align-items:center;gap:10px;font-size:20px;color:var(--sky)}
.call-label{left:105px;top:2180px;font-family:"Roboto",sans-serif;font-size:28px;color:var(--white)}
.call-number{left:352px;top:2177px;font-family:"Roboto Condensed",sans-serif;font-weight:700;font-size:33px;color:var(--white)}
.col-title{top:2312px;width:520px;text-align:center;font-family:"Raleway",sans-serif;font-size:33px;color:var(--navy)}
.col-title span{color:var(--sky)}
.news{left:143px;width:440px;display:flex;gap:16px}
.news-photo{width:116px;height:83px;flex:none;border:2px solid #444}
.news h4{font-family:"Roboto",sans-serif;font-weight:500;font-size:17px;color:var(--navy)}
.news .date{font-size:12px;color:var(--sky);margin:4px 0}
.news p{font-size:15px;line-height:19px;color:var(--grey)}
.news .more{margin-top:8px;font-size:13px}
.quote{left:700px;top:2368px;width:320px;text-align:center;font-size:16px;line-height:25px;color:var(--grey)}
.avatar{left:797px;top:2468px;width:130px;height:130px;border-radius:50%;border:2px solid #444}
.author{left:700px;top:2610px;width:320px;text-align:center;font-size:14px;color:var(--sky)}
.footer{left:0;top:2705px;width:1200px;height:198px;background:var(--sky);color:var(--white)}
.foot-links{left:79px;top:2734px;display:flex;gap:45px;font-size:19px}
.foot-rule{left:77px;top:2802px;width:1045px;height:1px;background:rgba(255,255,255,.7)}
.foot-item{display:flex;align-items:center;gap:16px;font-size:15px;line-height:22px}
.foot-icon{width:46px;height:46px;border-radius:50%;background:var(--white);display:flex;align-items:center;justify-content:center;flex:none}
.social{width:54px;height:54px;border-radius:50%;border:2px solid var(--white)}
</style>
</head>
<body>

<header>
  <div class="abs hero" role="img" aria-label="Hero photograph of a countertop being wiped clean"></div>
  <div class="brand brand-hero"><span class="brand-dot" style="width:34px;height:34px"></span>Bright Morrow Ltd</div>
  <nav class="abs nav">
    <a class="active" href="#">HOME</a>
    <a href="#" style="left:331px">ABOUT</a>
    <a href="#" style="left:499px">SERVICES</a>
    <a href="#" style="left:658px">BLOG</a>
    <a href="#" style="left:817px">CONTACT</a>
  </nav>
</header>

<section class="intro">
  <h1 class="abs welcome-title">WELCOME TO <span>BRIGHT CLEANING SERVICES</span></h1>
  <p class="abs welcome-text">Lorem Ipsum is simply dummy text of the printing and typesetting industry. Lorem Ipsum has been the industry's standard dummy text ever since the 1500s, when an unknown printer took a galley of type and scrambled it to make a type specimen book.</p>
  <div class="abs btn">READ MORE</div>
</section>

<section class="domestic-services">
  <div class="abs domestic" role="img" aria-label="Cleaner mopping a kitchen floor, tinted blue"></div>
  <h2 class="abs domestic-title">DOMESTIC SERVICES</h2>
  <svg class="abs" style="left:0;top:911px" width="1200" height="728">
    <g stroke="#ffffff" stroke-width="2" fill="none">
      <polyline points="302,167 412,167 532,283"/>
      <polyline points="302,523 412,523 532,407"/>
      <polyline points="898,167 788,167 668,283"/>
      <polyline points="898,523 788,523 668,407"/>
    </g>
  </svg>
  <div class="abs service-photo" style="left:110px;top:1016px;background:linear-gradient(135deg,#d9c9b4,#6c8fb8)" role="img" aria-label="Cleaner scrubbing a carpet"></div>
  <div class="abs service-photo" style="left:923px;top:1016px;background:linear-gradient(135deg,#c9a27a,#e9c53a)" role="img" aria-label="Person ironing clothes"></div>
  <div class="abs service-photo" style="left:110px;top:1318px;background:linear-gradient(135deg,#e6e8ea,#3b63a8)" role="img" aria-label="Cleaner mopping a tiled floor"></div>
  <div class="abs service-photo" style="left:923px;top:1318px;background:linear-gradient(135deg,#f0f0ec,#e8c94a)" role="img" aria-label="Cleaner with cleaning spray"></div>
  <div class="abs hub">Bright<br>Morrow Ltd</div>
  <div class="abs dom-label" style="left:43px;top:1201px"><h3>Carpet Cleaning</h3><p>Lorem Ipsum is simply dummy<br>text of the printing typesetting</p></div>
  <div class="abs dom-label" style="left:856px;top:1201px"><h3>Ironing</h3><p>Lorem Ipsum is simply dummy<br>text of the printing typesetting</p></div>
  <div class="abs dom-label" style="left:43px;top:1505px"><h3>Tiled Floor Steam Clean</h3><p>Lorem Ipsum is simply dummy<br>text of the printing typesetting</p></div>
  <div class="abs dom-label" style="left:856px;top:1505px"><h3>Tenancy Clean</h3><p>Lorem Ipsum is simply dummy<br>text of the printing typesetting</p></div>
</section>

<section class="commercial-services">
  <h2 class="abs section-title">COMMERCIAL <span>SERVICES</span></h2>
  <article class="abs card" style="left:77px">
    <div class="card-photo" style="background:linear-gradient(135deg,#e5e0d8,#8a5a3a)" role="img" aria-label="Cleaner vacuuming an office floor"></div>
    <h3>Vacuuming</h3><p>Lorem Ipsum is simply dummy<br>text of the printing typesetting</p>
    <div class="more">KNOW MORE <svg width="22" height="22"><circle cx="11" cy="11" r="10" fill="none" stroke="#3394f5" stroke-width="1.5"/><path d="M9 6l5 5-5 5" fill="none" stroke="#3394f5" stroke-width="1.5"/></svg></div>
  </article>
  <article class="abs card" style="left:346px">
    <div class="card-photo" style="background:linear-gradient(135deg,#f3f0ea,#e0c15a)" role="img" aria-label="Cleaner polishing a desk"></div>
    <h3>Desk polishing</h3><p>Lorem Ipsum is simply dummy<br>text of the printing typesetting</p>
    <div class="more">KNOW MORE <svg width="22" height="22"><circle cx="11" cy="11" r="10" fill="none" stroke="#3394f5" stroke-width="1.5"/><path d="M9 6l5 5-5 5" fill="none" stroke="#3394f5" stroke-width="1.5"/></svg></div>
  </article>
  <article class="abs card" style="left:615px">
    <div class="card-photo" style="background:linear-gradient(135deg,#b7b2a8,#6f7e6a)" role="img" aria-label="Worker wheeling a bin along a street"></div>
    <h3>Bin emptying</h3><p>Lorem Ipsum is simply dummy<br>text of the printing typesetting</p>
    <div class="more">KNOW MORE <svg width="22" height="22"><circle cx="11" cy="11" r="10" fill="none" stroke="#3394f5" stroke-width="1.5"/><path d="M9 6l5 5-5 5" fill="none" stroke="#3394f5" stroke-width="1.5"/></svg></div>
  </article>
  <article class="abs card" style="left:884px">
    <div class="card-photo" style="background:linear-gradient(135deg,#eceef0,#b9bec4)" role="img" aria-label="Cleaner cleaning a toilet"></div>
    <h3>Toilet cleaning</h3><p>Lorem Ipsum is simply dummy<br>text of the printing typesetting</p>
    <div class="more">KNOW MORE <svg width="22" height="22"><circle cx="11" cy="11" r="10" fill="none" stroke="#3394f5" stroke-width="1.5"/><path d="M9 6l5 5-5 5" fill="none" stroke="#3394f5" stroke-width="1.5"/></svg></div>
  </article>
</section>

<section class="call-band">
  <div class="abs call-grey"></div>
  <svg class="abs" style="left:77px;top:2129px" width="525" height="145"><polygon points="0,0 490,0 525,72 490,145 0,145" fill="#0a3a9c"/></svg>
  <div class="abs call-label">CALL US ON</div>
  <svg class="abs" style="left:275px;top:2168px" width="64" height="64"><circle cx="32" cy="32" r="29" fill="none" stroke="#fff" stroke-width="2"/><path d="M22 20c2-2 4-2 5 0l3 5c1 2 0 3-2 4 1 3 4 6 7 7 1-2 2-3 4-2l5 3c2 1 2 3 0 5-3 3-7 3-12-1-5-4-9-8-11-13-2-4-1-6 1-8z" fill="#fff"/></svg>
  <div class="abs call-number">555 010 2040</div>
  <p class="abs call-text">Lorem Ipsum is simply dummy text of the printing and typesetting industry. Lorem Ipsum has been the industry.</p>
  <div class="abs call-mail"><svg width="26" height="20"><rect x="1" y="1" width="24" height="18" fill="none" stroke="#3394f5" stroke-width="2"/><path d="M1 1l12 10 12-10" fill="none" stroke="#3394f5" stroke-width="2"/></svg>info@brightmorrow.co.uk</div>
</section>

<section class="news-block">
  <h2 class="abs col-title" style="left:57px">LATEST <span>NEWS</span></h2>
  <div class="abs" style="left:600px;top:2336px;width:1px;height:292px;background:var(--line)"></div>
  <article class="abs news" style="top:2382px">
    <div class="news-photo" style="background:linear-gradient(135deg,#e8dccb,#d9b04a)" role="img" aria-label="Cleaning team at work"></div>
    <div><h4>Lorem Ipsum is simply dummy text</h4><div class="date">&#9635; 10 JULY 2016</div><p>Lorem Ipsum is simply dummy text of the printing and typesetting industry......</p><div class="more">READ MORE &raquo;</div></div>
  </article>
  <div class="abs" style="left:135px;top:2510px;width:413px;height:1px;background:var(--line)"></div>
  <article class="abs news" style="top:2541px">
    <div class="news-photo" style="background:linear-gradient(135deg,#d8c2a4,#3f6fb4)" role="img" aria-label="Cleaning staff in uniform"></div>
    <div><h4>Lorem Ipsum is simply dummy text</h4><div class="date">&#9635; 10 JULY 2016</div><p>Lorem Ipsum is simply dummy text of the printing and typesetting industry......</p><div class="more">READ MORE &raquo;</div></div>
  </article>
</section>

<section class="testimonial">
  <h2 class="abs col-title" style="left:599px">CLIENT <span>TESTIMONIAL</span></h2>
  <p class="abs quote">Lorem Ipsum is simply dummy text of the printing and typesetting industry. Lorem Ipsum has been the industry's</p>
  <div class="abs avatar" style="background:linear-gradient(160deg,#e0d3c0,#8fa7c4)" role="img" aria-label="Portrait of a satisfied client"></div>
  <div class="abs author">- J. MARLOWE</div>
</section>

<footer>
  <div class="abs footer"></div>
  <div class="abs foot-links" style="color:#fff"><span>Home</span><span>About</span><span>Services</span><span>Blog</span><span>Contact</span></div>
  <div class="abs social" style="left:917px;top:2723px" aria-label="Social link"></div>
  <div class="abs social" style="left:993px;top:2723px" aria-label="Social link"></div>
  <div class="abs social" style="left:1068px;top:2723px" aria-label="Social link"></div>
  <div class="abs foot-rule"></div>
  <div class="abs foot-item" style="left:77px;top:2821px"><span class="foot-icon"><svg width="18" height="24"><path d="M9 1a8 8 0 0 1 8 8c0 6-8 14-8 14S1 15 1 9a8 8 0 0 1 8-8z" fill="#3394f5"/><circle cx="9" cy="9" r="3" fill="#fff"/></svg></span><span>Lorem Ipsum is simply<br>dummy text of the<br>printing.</span></div>
  <div class="abs foot-item" style="left:347px;top:2821px"><span class="foot-icon"><svg width="22" height="22"><path d="M4 3c2-2 4-2 5 0l2 4c1 2 0 3-2 4 1 3 3 5 6 6 1-2 2-3 4-2l3 2c2 1 1 3 0 4-3 2-7 1-11-3S1 7 4 3z" fill="#3394f5"/></svg></span><span>555 010 2040</span></div>
  <div class="abs foot-item" style="left:618px;top:2821px"><span class="foot-icon"><svg width="22" height="16"><rect x="1" y="1" width="20" height="14" fill="none" stroke="#3394f5" stroke-width="2"/><path d="M1 1l10 8 10-8" fill="none" stroke="#3394f5" stroke-width="2"/></svg></span><span>info@brightmorrow.co.uk</span></div>
  <div class="abs foot-item" style="left:889px;top:2821px"><span>© <b>BRIGHT MORROW</b>- 2016.<br>All Rights Reserved.</span></div>
</footer>

</body>
</html>
```